Harborline Renewal Business Card Design

Professional and clean design. The design colors should flow with the logo. Two-sided card with the website on the back which is:

www.HarborlineRenewal.example.

"Specializing in Water Damage Restoration"

On the front I need the name, email, phone, and logo.

Name: Darnell Quisby
Email: Darnell@HarborlineRenewal.example
Phone: 555-318-2046 for now

I only have the Preview and Thumbnail right now but should have the source files uploaded within a day or two.

Target Market(s)

Flood victims, home owners with water damage from busted pipes etc...

Industry/Entity Type

Business

Contact Information for Business Card

Name: Darnell Quisby

Font styles to use
Serif
Sans Serif

Requirements
Must have
• Business Card Details Info

```html
<!DOCTYPE html>
<html lang="en">
<head>
<meta charset="utf-8">
<title>Harborline Renewal Business Card</title>
<link rel="stylesheet" href="https://fonts.googleapis.com/css2?family=Cinzel:wght@600&family=Crimson+Text:wght@400;600&display=swap">
<style>
  :root {
    --canvas: #e9ecef;
    --card: #ffffff;
    --blue-deep: #1f7fcf;
    --blue-mid: #2a8fd6;
    --blue-light: #5bc0eb;
    --frame: #3a98dc;
  }
  * { box-sizing: border-box; margin: 0; padding: 0; }
  html, body { width: 1200px; height: 780px; overflow: hidden; }
  body {
    background: var(--canvas);
    display: flex;
    align-items: center;
    justify-content: center;
    gap: 40px;
    font-family: "Crimson Text", Georgia, serif;
  }
  .card {
    position: relative;
    width: 560px;
    height: 320px;
    background: var(--card);
    box-shadow: 0 6px 18px rgba(0,0,0,.15);
    overflow: hidden;
  }
  .card-frame {
    position: absolute;
    inset: 12px;
    border: 1px solid var(--frame);
    pointer-events: none;
  }
  .card-swoosh { position: absolute; left: 0; top: 0; }
  .brand {
    position: absolute;
    left: 224px;
    color: var(--blue-deep);
  }
  .brand-name {
    font-family: "Cinzel", "Times New Roman", serif;
    font-weight: 600;
    font-size: 24px;
    letter-spacing: 1px;
    line-height: 1.1;
    color: var(--blue-deep);
  }
  .brand-tagline {
    margin-top: 6px;
    font-size: 14px;
    color: var(--blue-mid);
  }
  .card-back .brand { top: 118px; }
  .back-website {
    position: absolute;
    right: 44px;
    bottom: 44px;
    font-size: 15px;
    color: var(--blue-mid);
  }
  .card-front .brand { top: 84px; }
  .holder-name {
    margin-top: 22px;
    font-family: "Cinzel", "Times New Roman", serif;
    font-weight: 600;
    font-size: 17px;
    letter-spacing: 1px;
    color: var(--blue-deep);
  }
  .contact-list { list-style: none; margin-top: 8px; }
  .contact-item {
    display: flex;
    align-items: center;
    gap: 8px;
    font-size: 14px;
    line-height: 1.5;
    color: var(--blue-mid);
  }
  .contact-icon { width: 12px; height: 12px; flex: none; }
</style>
</head>
<body>

  <section class="card card-back" aria-label="Card back">
    <svg class="card-swoosh" width="560" height="320" viewBox="0 0 560 320" aria-hidden="true">
      <circle cx="200" cy="160" r="150" fill="var(--blue-mid)"/>
      <circle cx="208" cy="160" r="144" fill="var(--blue-light)"/>
      <circle cx="222" cy="160" r="132" fill="var(--card)"/>
      <circle cx="130" cy="160" r="82" fill="var(--card)"/>
      <circle cx="130" cy="160" r="40" fill="var(--blue-mid)"/>
    </svg>
    <div class="brand">
      <div class="brand-name">Harborline Renewal</div>
      <div class="brand-tagline">Specializing in Water Damage Restoration</div>
    </div>
    <div class="back-website">www.HarborlineRenewal.example</div>
    <div class="card-frame"></div>
  </section>

  <section class="card card-front" aria-label="Card front">
    <svg class="card-swoosh" width="560" height="320" viewBox="0 0 560 320" aria-hidden="true">
      <circle cx="200" cy="160" r="150" fill="var(--blue-mid)"/>
      <circle cx="208" cy="160" r="144" fill="var(--blue-light)"/>
      <circle cx="222" cy="160" r="132" fill="var(--card)"/>
      <circle cx="130" cy="160" r="82" fill="var(--card)"/>
      <circle cx="130" cy="160" r="40" fill="var(--blue-mid)"/>
    </svg>
    <div class="brand">
      <div class="brand-name">Harborline Renewal</div>
      <div class="holder-name">DARNELL QUISBY</div>
      <ul class="contact-list">
        <li class="contact-item">
          <svg class="contact-icon" viewBox="0 0 16 16" aria-hidden="true"><path fill="var(--blue-mid)" d="M3 1h3l1 4-2 1.5a9 9 0 0 0 4.5 4.5L11 9l4 1v3a2 2 0 0 1-2 2A12 12 0 0 1 1 3a2 2 0 0 1 2-2z"/></svg>
          555-318-2046
        </li>
        <li class="contact-item">
          <svg class="contact-icon" viewBox="0 0 16 16" aria-hidden="true"><rect x="1" y="3" width="14" height="10" fill="var(--blue-mid)"/><path d="M1 3l7 6 7-6" fill="none" stroke="#fff" stroke-width="1.3"/></svg>
          Darnell@HarborlineRenewal.example
        </li>
        <li class="contact-item">
          <svg class="contact-icon" viewBox="0 0 16 16" aria-hidden="true"><circle cx="8" cy="8" r="7" fill="var(--blue-mid)"/><path d="M1 8h14M8 1c-3 3-3 11 0 14M8 1c3 3 3 11 0 14" fill="none" stroke="#fff" stroke-width="1"/></svg>
          www.HarborlineRenewal.example
        </li>
      </ul>
    </div>
    <div class="card-frame"></div>
  </section>

</body>
</html>
```